Moxy Fen needs some awesome stationary

Do you have what it takes to get my brand? You either do or you don't, have a crack at a design and you my just win my business.

I don't want to waste your or my time, so put your creative genius on either a business card or envelope.

I however need a package of stationary that follows the same brand. I will message you to complete the remaining should I like your first submission.

Here is what I need, have a go!

Basically I need the following for my small business based in melbourne.
- Letterhead (printer ready and MS Word)
- Business Card
- Compliments Slip
- Envelope
- Proposal Cover Page (MS Word only)
- Presentation Folder
- Marbled Fox Cards
- Student Name Tent
- Index Cards
- Vell-Ka

I am establishing the brand and it must be modern, professional but also relaxed; that is not formal and not corporate. It represents a company are leaders, but small enough to care and operate like a bunch of friends. We are bringing people and conversations back to business, and turfing out all the bureaucracy and crazy and wasteful procedures. Its about "lets talk and figure it out together and find even better ways".

Target Market(s)

Mainly companies that build software products, but Agile practices are used in many other industries (even graphic design projects)

Industry/Entity Type

Information Technology

Font styles to use
Sans Serif

Colors
3176b5
aaaaaa

Requirements
Must have
• I like curves and circles and not boxes or rectangles.
• I want a colour rich design with my brand colours, but it must be balanced.
• I want more modern than traditional, but simple modern
Should not have
• Not corporate
• Please don't waste my time if your not going to think about it.
• Don't mess with my primary logo
• Don't change my colours
• Don't overlay logo on image

```html
<!DOCTYPE html>
<html lang="en">
<head>
<meta charset="utf-8">
<title>Moxy Fen – Business Card</title>
<link rel="stylesheet" href="https://fonts.googleapis.com/css2?family=Open+Sans:wght@400;600;700&display=swap">
<style>
  :root {
    --brand-blue: #2c5aa0;
    --brand-grey: #8f9aab;
    --paper: #ffffff;
    --ink: #4a4a4a;
    --backdrop: #e4e4e4;
  }
  * { box-sizing: border-box; margin: 0; padding: 0; }
  html, body {
    width: 1200px; height: 987px; overflow: hidden;
    background: var(--backdrop);
    font-family: "Open Sans", Arial, sans-serif;
  }
  .canvas { position: relative; width: 1200px; height: 987px; }

  .card {
    position: absolute; left: 293px; width: 616px; height: 352px;
    border-radius: 16px; overflow: hidden;
  }
  .card--front { top: 130px; background: var(--paper); }
  .card--back { top: 505px; background: var(--brand-blue); }

  /* front band */
  .band { position: absolute; left: 0; top: 52px; width: 100%; height: 83px; display: flex; }
  .band__blue { width: 410px; background: var(--brand-blue); }
  .band__grey { flex: 1; background: var(--brand-grey); }

  .identity { position: absolute; left: 30px; top: 64px; color: #fff; }
  .identity__name { font-size: 22px; font-weight: 700; line-height: 1.2; }
  .identity__role { font-size: 16px; font-weight: 400; line-height: 1.3; margin-left: 2px; }

  .brand-mark { position: absolute; left: 370px; top: 50px; width: 150px; height: 120px; }
  .brand-mark__dot {
    position: absolute; left: 22px; top: 4px; width: 80px; height: 80px;
    border-radius: 50%; background: var(--paper); border: 6px solid var(--brand-blue);
  }
  .brand-mark__name {
    position: absolute; left: 0; top: 85px; white-space: nowrap;
    font-size: 26px; font-weight: 700; color: var(--brand-blue);
  }

  .contacts { position: absolute; left: 32px; top: 236px; list-style: none; }
  .contacts li {
    display: flex; align-items: center; gap: 8px;
    font-size: 15px; color: var(--ink); height: 23.5px;
  }
  .contacts svg { width: 15px; height: 15px; fill: var(--brand-blue); flex: none; }

  .address {
    position: absolute; right: 40px; top: 258px; text-align: right;
    font-size: 15px; color: var(--ink); line-height: 23px; font-style: normal;
  }

  /* back */
  .back-mark {
    position: absolute; left: 0; right: 0; top: 140px;
    display: flex; justify-content: center; align-items: center; gap: 18px;
  }
  .back-mark__dot { width: 58px; height: 58px; border-radius: 50%; background: var(--brand-grey); }
  .back-mark__name { font-size: 46px; font-weight: 700; color: #fff; }
  .back-url {
    position: absolute; left: 0; right: 0; top: 294px; text-align: center;
    font-size: 14px; color: #fff; letter-spacing: 0.42em;
  }
</style>
</head>
<body>
<main class="canvas">

  <section class="card card--front" aria-label="Business card front">
    <div class="band"><div class="band__blue"></div><div class="band__grey"></div></div>

    <div class="identity">
      <p class="identity__name">Dara Quill</p>
      <p class="identity__role">CEO, Professional Scrum Trainer</p>
    </div>

    <div class="brand-mark">
      <span class="brand-mark__dot"></span>
      <span class="brand-mark__name">Moxy Fen</span>
    </div>

    <ul class="contacts">
      <li>
        <svg viewBox="0 0 24 24" aria-hidden="true"><path d="M6.6 10.8a15.1 15.1 0 0 0 6.6 6.6l2.2-2.2a1 1 0 0 1 1-.25 11.4 11.4 0 0 0 3.6.57 1 1 0 0 1 1 1V20a1 1 0 0 1-1 1A17 17 0 0 1 3 4a1 1 0 0 1 1-1h3.5a1 1 0 0 1 1 1c0 1.25.2 2.45.57 3.57a1 1 0 0 1-.25 1z"/></svg>
        1300MOXYFN
      </li>
      <li>
        <svg viewBox="0 0 24 24" aria-hidden="true"><path d="M7 1h10a2 2 0 0 1 2 2v18a2 2 0 0 1-2 2H7a2 2 0 0 1-2-2V3a2 2 0 0 1 2-2zm0 3v14h10V4zm5 15.2a1.2 1.2 0 1 0 0 2.4 1.2 1.2 0 0 0 0-2.4z"/></svg>
        +61 400 555 218
      </li>
      <li>
        <svg viewBox="0 0 24 24" aria-hidden="true"><path d="M2 5h20v14H2zm2 2v.4l8 5.2 8-5.2V7zm0 2.8V17h16V9.8l-8 5.2z"/></svg>
        dara@moxy-fen.com.au
      </li>
      <li>
        <svg viewBox="0 0 24 24" aria-hidden="true"><path d="M12 2a10 10 0 1 0 0 20 10 10 0 0 0 0-20zm-1 17.9A8 8 0 0 1 4.1 10L9 15v1a2 2 0 0 0 2 2zm6.9-2.5A2 2 0 0 0 16 16h-1v-3a1 1 0 0 0-1-1H8v-2h2a1 1 0 0 0 1-1V7h2a2 2 0 0 0 2-2v-.4a8 8 0 0 1 2.9 12.8z"/></svg>
        www.moxy-fen.com.au
      </li>
    </ul>

    <address class="address">
      PO Box 4417<br>
      Elmbrook North<br>
      VIC 3999, Australia
    </address>
  </section>

  <section class="card card--back" aria-label="Business card back">
    <div class="back-mark">
      <span class="back-mark__dot"></span>
      <span class="back-mark__name">Moxy Fen</span>
    </div>
    <p class="back-url">www.moxy-fen.com.au</p>
  </section>

</main>
</body>
</html>
```